Marlow Vale Stud website

We would like to create a horse stud/agistment farm website similar to this websites we have attached below:
www.thornbeck.com.au
www.quillstead.com.au
www.brackley.com
www.pimsey.com.au
The main colour scheme are purple and white to align with the stable's racing colours.
We have also attach the company logo and also images of the farm and create some ideas for the website.
Many thanks for looking into this project!

```html
<!DOCTYPE html>
<html lang="en">
<head>
<meta charset="utf-8">
<title>Marlow Vale Stud</title>
<link href="https://fonts.googleapis.com/css2?family=Open+Sans:wght@400;600;700;800&family=Oswald:wght@500&display=swap" rel="stylesheet">
<style>
:root{
  --purple:#2e0f33;
  --purple-mid:#3d1744;
  --purple-deep:#24092a;
  --accent:#5b1f63;
  --white:#ffffff;
  --grey-bg:#ececec;
  --text:#333333;
  --muted:#777777;
}
*{box-sizing:border-box;margin:0;padding:0}
html,body{width:1200px;height:3040px;overflow:hidden}
body{font-family:"Open Sans",Arial,sans-serif;color:var(--text);background:var(--white);position:relative}
section,header,footer,nav,div{position:relative}

/* top bar */
.top-bar{height:40px;background:var(--purple);display:flex;align-items:center;justify-content:space-between;padding:0 110px}
.region-links{display:flex;gap:26px;font-size:12px;color:#e6d9e8}
.social-row{display:flex;gap:8px}
.social-dot{width:26px;height:26px;border-radius:50%;border:1.5px solid var(--white)}

/* header */
.site-header{height:120px;display:flex;align-items:center;justify-content:space-between;padding:0 110px;background:var(--white)}
.brand{display:flex;align-items:center;gap:12px;font-weight:700;font-size:22px;color:var(--purple)}
.brand-dot{width:46px;height:46px;border-radius:50%;background:var(--purple)}
.main-nav{display:flex;gap:30px;font-size:13px;font-weight:600;color:#555}
.main-nav .active{color:var(--purple);border-bottom:2px solid var(--purple);padding-bottom:4px}

/* hero */
.hero{height:610px;background:linear-gradient(180deg,#6d7f92 0%,#8e8a78 38%,#4f5a32 62%,#37421f 100%)}
.hero-title{position:absolute;left:110px;top:192px;background:rgba(255,255,255,.85);padding:8px 22px;font-family:"Oswald",sans-serif;font-size:40px;letter-spacing:1px;color:#2a2a2a}
.hero-sub{position:absolute;left:110px;top:262px;background:rgba(30,30,30,.7);padding:6px 22px;font-size:22px;color:var(--white);letter-spacing:.5px}
.hero-dots{position:absolute;left:0;right:0;bottom:28px;display:flex;justify-content:center;gap:10px}
.hero-dots span{width:12px;height:12px;border-radius:50%;background:rgba(255,255,255,.55)}
.hero-dots span.on{background:var(--white)}

/* section headings */
.section-title{text-align:center;font-size:34px;font-weight:800;color:var(--purple);letter-spacing:.5px}
.title-rule{width:70px;height:3px;background:var(--purple);margin:14px auto 0}

/* welcome */
.welcome{height:480px;padding-top:62px}
.card-row{display:flex;gap:16px;justify-content:center;margin-top:58px}
.card{width:232px}
.card-photo{height:186px}
.card-caption{height:44px;background:var(--purple);color:var(--white);font-size:13px;font-weight:600;display:flex;align-items:center;justify-content:center;letter-spacing:.5px}
.slider-arrow{position:absolute;top:248px;width:24px;height:40px}
.slider-arrow.left{left:52px}
.slider-arrow.right{right:52px}

/* feature */
.feature{height:450px;background:var(--purple);display:flex;align-items:center;padding:0 110px}
.feature-photo{width:510px;height:420px;background:linear-gradient(180deg,#7b8f6e 0%,#b6b0a0 45%,#4e7a2f 80%,#3c6624 100%)}
.feature-box{width:470px;height:420px;background:var(--white);padding:56px 40px}
.feature-box h3{font-size:24px;font-weight:600;line-height:1.35;color:var(--purple);text-transform:uppercase}
.feature-box p{margin-top:26px;font-size:13px;line-height:1.6;color:var(--muted)}

/* gallery */
.gallery{height:680px;padding-top:92px}
.gallery-row{display:flex;gap:4px;margin-top:56px}
.gallery-photo{flex:1;height:290px}
.gallery-btn{display:block;width:210px;margin:64px auto 0;background:var(--purple);color:var(--white);font-size:13px;font-weight:700;text-align:center;padding:14px 0;letter-spacing:.5px}

/* newsletter */
.newsletter{height:360px;background:var(--grey-bg);padding-top:70px}
.newsletter-sub{text-align:center;font-size:13px;color:#666;margin-top:18px}
.signup{display:flex;justify-content:center;gap:14px;margin-top:40px}
.field{width:380px;height:50px;background:var(--white);border:1px solid #cfcfcf;font-size:14px;color:#888;padding:0 16px;display:flex;align-items:center}
.signup-btn{width:190px;height:50px;background:var(--purple);color:var(--white);font-size:13px;font-weight:700;display:flex;align-items:center;justify-content:center;letter-spacing:.5px}

/* footer */
.site-footer{height:300px;background:var(--purple);color:#e9dfeb;text-align:center;padding-top:56px}
.footer-social{display:flex;justify-content:center;gap:16px}
.footer-social .social-dot{width:44px;height:44px;border-width:2px}
.contact-line{display:flex;justify-content:center;gap:40px;margin-top:38px;font-size:14px;align-items:center}
.contact-line span{display:flex;align-items:center;gap:8px}
.legal-links{display:flex;justify-content:center;gap:14px;margin-top:22px;font-size:14px}
.copyright{margin-top:26px;font-size:13px}
</style>
</head>
<body>

<div class="top-bar">
  <div class="region-links"><span>Ireland</span><span>America</span><span>Australia</span><span>National Hunt</span><span>Refurbish</span></div>
  <div class="social-row"><span class="social-dot"></span><span class="social-dot"></span><span class="social-dot"></span><span class="social-dot"></span></div>
</div>

<header class="site-header">
  <div class="brand"><span class="brand-dot"></span>Marlow Vale Stud</div>
  <nav class="main-nav"><span class="active">HOME</span><span>ABOUT US</span><span>STALLIONS</span><span>VIDEOS</span><span>GALLERY</span><span>CONTACT</span></nav>
</header>

<section class="hero" role="img" aria-label="Farm paddock at dusk with wooden fences and trees">
  <h1 class="hero-title">HORSE STUD/AGISTMENT FARM</h1>
  <p class="hero-sub">Nostrud Exercitation Ullamco Laboris</p>
  <div class="hero-dots"><span class="on"></span><span></span><span></span></div>
</section>

<section class="welcome">
  <h2 class="section-title">WELCOME TO MARLOW VALE STUD</h2>
  <div class="title-rule"></div>
  <svg class="slider-arrow left" viewBox="0 0 24 40"><path d="M18 4 L6 20 L18 36" fill="none" stroke="#999" stroke-width="3"/></svg>
  <svg class="slider-arrow right" viewBox="0 0 24 40"><path d="M6 4 L18 20 L6 36" fill="none" stroke="#999" stroke-width="3"/></svg>
  <div class="card-row">
    <div class="card"><div class="card-photo" role="img" aria-label="Chestnut horse standing in a paddock" style="background:linear-gradient(180deg,#5d7a3a,#8a6a3e)"></div><div class="card-caption">NUMQUAM EIUS MODI</div></div>
    <div class="card"><div class="card-photo" role="img" aria-label="Green farm field under a cloudy sky" style="background:linear-gradient(180deg,#8fa4b6,#4f7a2e)"></div><div class="card-caption">NOSTRUD EXERCITAT</div></div>
    <div class="card"><div class="card-photo" role="img" aria-label="Grey horse grazing in an open field" style="background:linear-gradient(180deg,#aab7c0,#6a8a45)"></div><div class="card-caption">DOLOREM IPSUM QUIA</div></div>
    <div class="card"><div class="card-photo" role="img" aria-label="Group of horses standing together" style="background:linear-gradient(180deg,#a7b9cc,#4a3a2c)"></div><div class="card-caption">BEATAE VITAE DICTA</div></div>
  </div>
</section>

<section class="feature">
  <div class="feature-photo" role="img" aria-label="Racehorse with jockey in purple silks on the track"></div>
  <div class="feature-box">
    <h3>Excepteur sint occaecat cupidatat non proident, sunt in culpa qui officia deserunt mollit anim</h3>
    <p>Sed ut perspiciatis unde omnis iste natus error sit voluptatem accusantium doloremque laudantium, totam rem aperiam, eaque ipsa quae.</p>
  </div>
</section>

<section class="gallery">
  <h2 class="section-title">OUR GALLERY</h2>
  <div class="title-rule"></div>
  <div class="gallery-row">
    <div class="gallery-photo" role="img" aria-label="Aerial view of farm buildings and hills" style="background:linear-gradient(180deg,#8fb0cf,#6e8a4a)"></div>
    <div class="gallery-photo" role="img" aria-label="Stable yards and paddocks from above" style="background:linear-gradient(180deg,#7e9a5a,#4f7a2e)"></div>
    <div class="gallery-photo" role="img" aria-label="Tree-lined gravel driveway" style="background:linear-gradient(180deg,#3e5a2a,#b59a6a)"></div>
    <div class="gallery-photo" role="img" aria-label="Open pasture under a blue sky" style="background:linear-gradient(180deg,#6f9bd0,#5a8a3a)"></div>
  </div>
  <span class="gallery-btn">VIEW MORE GALLERY</span>
</section>

<section class="newsletter">
  <h2 class="section-title">NEWSLETTER SUBSCRIBE</h2>
  <div class="title-rule"></div>
  <p class="newsletter-sub">Be the first to discover our latest news &amp; stallion updates</p>
  <div class="signup">
    <div class="field">Your Name</div>
    <div class="field">Your Email</div>
    <div class="signup-btn">SUBSCRIBE NOW</div>
  </div>
</section>

<footer class="site-footer">
  <div class="footer-social"><span class="social-dot"></span><span class="social-dot"></span><span class="social-dot"></span><span class="social-dot"></span></div>
  <div class="contact-line">
    <span><svg width="12" height="16" viewBox="0 0 12 16"><path d="M6 0a6 6 0 0 0-6 6c0 4.5 6 10 6 10s6-5.5 6-10a6 6 0 0 0-6-6zm0 8.5A2.5 2.5 0 1 1 6 3.5a2.5 2.5 0 0 1 0 5z" fill="#e9dfeb"/></svg>Marlow Vale Stud 48 Ridgeway Lane</span>
    <span><svg width="14" height="14" viewBox="0 0 14 14"><path d="M3 0l2.5 3.5-1.5 1.5c.8 1.8 2.2 3.2 4 4l1.5-1.5L14 10l-1.5 3C6 13 1 8 1 1.5z" fill="#e9dfeb"/></svg>(+61) 20-5550-0147</span>
    <span><svg width="16" height="12" viewBox="0 0 16 12"><rect x="0.5" y="0.5" width="15" height="11" fill="none" stroke="#e9dfeb"/><path d="M0.5 0.5 L8 7 L15.5 0.5" fill="none" stroke="#e9dfeb"/></svg>info@marlowvalestud.com</span>
  </div>
  <div class="legal-links"><span>Help</span><span>|</span><span>About</span><span>|</span><span>Terms and Conditions</span><span>|</span><span>Privacy</span><span>|</span><span>FAQ</span></div>
  <p class="copyright">Copyrights © 2015, Marlow Vale Stud. All rights reserved.</p>
</footer>

</body>
</html>
```